Veltrano.co - Polar Expeditions Specialists

We need a modern, visually striking business card for Veltrano.co, a company specialized in selling expedition cruises to the most remote regions on Earth, with a focus on the Arctic and Antarctica. The design should instantly communicate that the cardholder is an expert in polar travel. Use clean, premium aesthetics with cool tones like icy blue and white, possibly incorporating polar imagery (ice, glaciers, penguins, etc.)

Attached the logo

Contact Information for Business Card

Feels high-end and trustworthy.. Visually memorable — encourages people to keep it

Colors
0054AA
0677BA
7BADD7
CADEEF
E8F1F8

Requirements
Must have
• ice, glaciers, penguins, montains
Nice to have
• modern, transparente,

```html
<!DOCTYPE html>
<html lang="en">
<head>
<meta charset="utf-8">
<title>Veltrano.co – Business Card</title>
<link href="https://fonts.googleapis.com/css2?family=Poppins:wght@400;500;600;700&display=swap" rel="stylesheet">
<style>
  :root {
    --stage: #2b2b2e;
    --card-white: #ffffff;
    --brand-blue: #3473b8;
    --brand-deep: #0054aa;
    --ice-light: #cadeef;
    --ice-pale: #e8f1f8;
    --ink: #1f2430;
  }
  * { margin: 0; padding: 0; box-sizing: border-box; }
  html, body {
    width: 1200px; height: 1195px; overflow: hidden;
    background: var(--stage);
    font-family: "Poppins", sans-serif;
  }
  .stage {
    width: 1200px; height: 1195px;
    display: flex; align-items: center; justify-content: center; gap: 80px;
  }
  .card {
    width: 500px; height: 860px; border-radius: 38px;
    position: relative; overflow: hidden;
  }
  /* Front */
  .card-front {
    background: var(--card-white);
    display: flex; flex-direction: column; align-items: center;
    text-align: center; color: var(--ink);
  }
  .brand {
    margin-top: 110px;
    display: flex; flex-direction: column; align-items: center;
  }
  .brand-mark {
    width: 40px; height: 40px; border-radius: 50%;
    background: var(--brand-blue); margin-bottom: 24px;
  }
  .brand-name {
    font-weight: 700; font-size: 74px; line-height: 1;
    color: var(--brand-blue); letter-spacing: -1px;
  }
  .brand-tagline {
    font-weight: 600; font-size: 24px; color: var(--brand-blue);
    margin-top: 6px; line-height: 1.2;
  }
  .person { margin-top: 140px; }
  .person-name { font-weight: 700; font-size: 32px; color: var(--brand-blue); line-height: 1.2; }
  .person-role { font-weight: 400; font-size: 17px; margin-top: 2px; }
  .divider {
    width: 80px; height: 2px; background: var(--brand-blue);
    margin: 22px auto;
  }
  .contact-list { list-style: none; font-size: 18px; line-height: 1.4; }
  .address { font-size: 18px; line-height: 1.4; font-style: normal; }
  /* Back */
  .card-back {
    background: var(--brand-blue); color: var(--card-white);
  }
  .back-pattern {
    position: absolute; inset: 0 0 200px 0;
    background: linear-gradient(180deg, var(--ice-pale) 0%, var(--ice-light) 30%, rgba(123,173,215,0.6) 60%, rgba(52,115,184,0) 100%);
    opacity: 0.7;
  }
  .back-brand {
    position: absolute; left: 44px; right: 36px; bottom: 70px;
    display: flex; align-items: center; gap: 22px;
  }
  .back-brand .brand-mark { width: 60px; height: 60px; background: var(--card-white); margin: 0; flex: none; }
  .back-brand .brand-name { color: var(--card-white); font-size: 60px; }
  .back-brand .brand-tagline { color: var(--card-white); font-size: 19px; margin-top: 4px; }
</style>
</head>
<body>
<main class="stage">
  <section class="card card-front" aria-label="Business card front">
    <div class="brand">
      <span class="brand-mark"></span>
      <div class="brand-name">Veltrano.co</div>
      <div class="brand-tagline">Polar Expeditions Specialists</div>
    </div>
    <div class="person">
      <div class="person-name">Marlow Quist</div>
      <div class="person-role">CEO &amp; Founder</div>
    </div>
    <div class="divider"></div>
    <ul class="contact-list">
      <li>+1.555.010.482</li>
      <li>hello@veltrano.co</li>
      <li>www.veltrano.co</li>
    </ul>
    <div class="divider"></div>
    <address class="address">48 Harbor Crest Lane<br>Fairhollow, NJ 07321 USA</address>
  </section>

  <section class="card card-back" aria-label="Business card back">
    <div class="back-pattern" role="img" aria-label="Polar imagery: rows of pale icy-blue polar animal figures on ice with small stars, fading into the blue toward the bottom"></div>
    <div class="back-brand">
      <span class="brand-mark"></span>
      <div>
        <div class="brand-name">Veltrano.co</div>
        <div class="brand-tagline">Polar Expeditions Specialists</div>
      </div>
    </div>
  </section>
</main>
</body>
</html>
```